Health Care Company with Logo Needs Business Cards designed

We are a luxury behavioral health company looking for business cards design we already have a logo and are looking for someone to design a sophisticated luxurious looking business card. Please note that Card design should be captivating just like the logo and also encompass the logo color

Industry/Entity Type

Healthcare

Contact Information for Business Card

Logo,company name, tagline, my name and title, contact details, and physical address

```html
<!DOCTYPE html>
<html lang="en">
<head>
<meta charset="utf-8">
<title>Marlow Behavioral Health – Business Cards</title>
<link rel="stylesheet" href="https://fonts.googleapis.com/css2?family=Roboto:ital,wght@0,400;0,500;1,400&display=swap">
<style>
  :root {
    --backdrop: #2a2a2a;
    --paper: #f1f1f1;
    --paper-shade: #e6e6e6;
    --purple: #73317f;
    --purple-deep: #6a2c78;
    --blue: #1a93d1;
    --orange: #dc860f;
    --ink-light: #ffffff;
    --ink-soft: #5f5f66;
  }
  html, body {
    margin: 0;
    padding: 0;
    width: 1200px;
    height: 1138px;
    overflow: hidden;
    background: var(--backdrop);
  }
  .sheet {
    position: relative;
    width: 1200px;
    height: 1138px;
  }
  .card {
    position: absolute;
    border-radius: 16px;
    overflow: hidden;
    background: linear-gradient(160deg, var(--paper) 0%, var(--paper-shade) 100%);
  }
  .card-front {
    left: 274px;
    top: 186px;
    width: 623px;
    height: 376px;
  }
  .front-brand {
    position: absolute;
    left: 0;
    right: 0;
    top: 150px;
    text-align: center;
  }
  .brand-name {
    margin: 0;
    font-family: "Roboto", Arial, sans-serif;
    font-weight: 500;
    font-size: 42px;
    line-height: 1;
    color: var(--purple);
  }
  .brand-tagline {
    margin: 12px 0 0;
    font-family: "Roboto", Arial, sans-serif;
    font-weight: 400;
    font-size: 16px;
    color: var(--ink-soft);
  }
  .card-back {
    left: 276px;
    top: 608px;
    width: 618px;
    height: 374px;
  }
  .card-back svg {
    display: block;
    width: 618px;
    height: 374px;
  }
  .back-brand-name {
    font-family: "Roboto", Arial, sans-serif;
    font-weight: 500;
    font-size: 27px;
    fill: var(--purple);
  }
  .back-brand-tagline {
    font-family: "Roboto", Arial, sans-serif;
    font-weight: 400;
    font-size: 13px;
    fill: var(--ink-soft);
  }
  .person-name {
    font-family: "Roboto", Arial, sans-serif;
    font-weight: 500;
    font-size: 31px;
    fill: var(--ink-light);
  }
  .person-title {
    font-family: "Roboto", Arial, sans-serif;
    font-style: italic;
    font-size: 20px;
    fill: var(--ink-light);
  }
  .contact-line {
    font-family: "Roboto", Arial, sans-serif;
    font-size: 20px;
    fill: var(--ink-light);
  }
  .contact-icon {
    fill: none;
    stroke: var(--ink-light);
    stroke-width: 1.6;
  }
  .contact-icon-solid {
    fill: var(--ink-light);
  }
</style>
</head>
<body>
<main class="sheet">

  <section class="card card-front" aria-label="Business card front">
    <div class="front-brand">
      <h1 class="brand-name">Marlow Behavioral Health</h1>
      <p class="brand-tagline">Steady care for every step forward</p>
    </div>
  </section>

  <section class="card card-back" aria-label="Business card back">
    <svg viewBox="0 0 773 468" xmlns="http://www.w3.org/2000/svg">
      <defs>
        <linearGradient id="purpleBand" x1="0" y1="0" x2="0" y2="1">
          <stop offset="0" stop-color="var(--purple)"/>
          <stop offset="1" stop-color="var(--purple-deep)"/>
        </linearGradient>
      </defs>

      <path class="band-purple" fill="url(#purpleBand)"
            d="M0,375 C160,402 330,360 480,232 C600,130 680,88 773,82 L773,468 L0,468 Z"/>
      <path class="band-blue" fill="none" stroke="var(--blue)" stroke-width="7" stroke-linecap="round"
            d="M62,328 C250,342 370,252 482,160 C600,70 690,52 773,49"/>
      <path class="band-orange" fill="var(--orange)"
            d="M0,322 C120,344 262,338 388,263 C272,334 130,366 0,360 Z"/>

      <text class="back-brand-name" x="48" y="200">Marlow Behavioral Health</text>
      <text class="back-brand-tagline" x="48" y="222">Steady care for every step forward</text>

      <text class="person-name" x="721" y="245" text-anchor="end">DANIEL REESE</text>
      <text class="person-title" x="721" y="273" text-anchor="end">Managing Director</text>

      <text class="contact-line" x="681" y="330" text-anchor="end">555-010-0147</text>
      <text class="contact-line" x="681" y="358" text-anchor="end">marlowbehavioral.com</text>
      <text class="contact-line" x="681" y="386" text-anchor="end">daniel@marlowbehavioral.com</text>
      <text class="contact-line" x="721" y="418" text-anchor="end">48, Cedar Lane, Any Town, US 123456</text>

      <g class="icon-phone" transform="translate(702,316)">
        <path class="contact-icon-solid" d="M2,5 C2,2 18,2 18,5 L18,7 L14,7 L13,5 L7,5 L6,7 L2,7 Z"/>
        <path class="contact-icon-solid" d="M5,8 L15,8 L17,15 L3,15 Z"/>
      </g>
      <g class="icon-mail" transform="translate(702,345)">
        <rect class="contact-icon" x="1" y="1" width="17" height="12"/>
        <path class="contact-icon" d="M1,1 L9.5,8 L18,1 M1,13 L7,6.5 M18,13 L12,6.5"/>
      </g>
      <g class="icon-globe" transform="translate(711,380)">
        <circle class="contact-icon" cx="0" cy="0" r="8"/>
        <ellipse class="contact-icon" cx="0" cy="0" rx="3.5" ry="8"/>
        <path class="contact-icon" d="M-8,0 L8,0 M-7,-4 L7,-4 M-7,4 L7,4"/>
      </g>
    </svg>
  </section>

</main>
</body>
</html>
```